business card deign

Logo needs the following on it.
1. attached logo
2. Tagline - "If it keeps a drink cold or the party going...we do it!"
3. Name- Dalton Pikes, Founder and CPO
4. Address - 412 E. Carver Avenue, Ste 2207, Tampa, FL. 33917
5. Phone - 555.318.4726

```html
<!DOCTYPE html>
<html lang="en">
<head>
<meta charset="utf-8">
<title>Koolbo Business Card</title>
<link href="https://fonts.googleapis.com/css2?family=Montserrat:wght@400;500;700&family=Roboto:wght@700&display=swap" rel="stylesheet">
<style>
  :root {
    --stage: #3b3532;
    --card: #ffffff;
    --ink: #141414;
    --ink-soft: #3a3a3a;
    --rule: #2b2b2b;
    --pattern-dark: #1a1a1a;
    --pattern-light: #f2f2f2;
  }
  * { margin: 0; padding: 0; box-sizing: border-box; }
  html, body { width: 1200px; height: 786px; overflow: hidden; }
  body { background: var(--stage); font-family: "Montserrat", sans-serif; color: var(--ink); position: relative; }

  .card {
    position: absolute; top: 233px; width: 560px; height: 320px;
    background: var(--card); box-shadow: 0 10px 30px rgba(0,0,0,.45);
  }
  .card--front { left: 30px; }
  .card--back { left: 610px; }

  .brand {
    position: absolute; left: 40px; top: 150px; width: 190px;
    display: flex; align-items: center; gap: 10px;
  }
  .brand__dot { width: 22px; height: 22px; border-radius: 50%; background: var(--ink); flex: none; }
  .brand__name { font-family: "Roboto", sans-serif; font-weight: 700; font-size: 26px; letter-spacing: 8px; color: var(--ink); }

  .divider { position: absolute; left: 252px; top: 62px; width: 1.5px; height: 150px; background: var(--rule); }

  .details { position: absolute; left: 268px; top: 56px; }
  .details__name { font-size: 21px; font-weight: 700; line-height: 1.1; }
  .details__title { font-size: 11px; color: var(--ink-soft); margin-top: 2px; }
  .details__address { font-size: 11.5px; color: var(--ink-soft); line-height: 1.35; margin: 16px 0 12px 22px; }
  .contact { list-style: none; }
  .contact li { display: flex; align-items: center; gap: 8px; font-size: 11.5px; color: var(--ink-soft); margin-bottom: 7px; }
  .contact svg { width: 12px; height: 12px; flex: none; }

  .tagline { position: absolute; left: 0; right: 0; bottom: 40px; text-align: center; font-size: 13px; font-weight: 500; color: var(--ink); }

  .pattern {
    position: absolute; inset: 14px 0 14px 0;
    background: repeating-linear-gradient(180deg, var(--pattern-light) 0 40px, var(--pattern-dark) 40px 42px),
                linear-gradient(90deg, #d9d9d9, #bdbdbd);
    background-blend-mode: multiply;
  }
  .back-brand {
    position: absolute; left: 50%; top: 50%; transform: translate(-50%, -50%);
    background: var(--card); padding: 6px 18px;
    font-family: "Roboto", sans-serif; font-weight: 700; font-size: 24px; letter-spacing: 7px; color: var(--ink);
  }
</style>
</head>
<body>
  <section class="card card--front">
    <div class="brand">
      <span class="brand__dot"></span>
      <span class="brand__name">KOOLBO</span>
    </div>
    <div class="divider"></div>
    <div class="details">
      <p class="details__name">Dalton Pikes</p>
      <p class="details__title">Founder and CPO</p>
      <p class="details__address">412 E. Carver Avenue, Ste 2207,<br>Tampa, FL. 33917</p>
      <ul class="contact">
        <li><svg viewBox="0 0 24 24"><path fill="currentColor" d="M6.6 10.8a15 15 0 0 0 6.6 6.6l2.2-2.2c.3-.3.7-.4 1-.2 1.1.4 2.3.6 3.6.6.6 0 1 .4 1 1V20c0 .6-.4 1-1 1A17 17 0 0 1 3 4c0-.6.4-1 1-1h3.5c.6 0 1 .4 1 1 0 1.3.2 2.5.6 3.6.1.3 0 .7-.2 1z"/></svg>555.318.4726</li>
        <li><svg viewBox="0 0 24 24"><path fill="currentColor" d="M2 5h20v14H2zm2 2v.5l8 5 8-5V7l-8 5z"/></svg>info@koolbo.com</li>
        <li><svg viewBox="0 0 24 24"><circle cx="12" cy="12" r="9" fill="none" stroke="currentColor" stroke-width="2"/><path d="M3 12h18M12 3c3 3 3 15 0 18M12 3c-3 3-3 15 0 18" fill="none" stroke="currentColor" stroke-width="1.6"/></svg>www.koolbo.com</li>
      </ul>
    </div>
    <p class="tagline">If it keeps a drink cold or the party going...we do it</p>
  </section>

  <section class="card card--back">
    <div class="pattern" role="img" aria-label="Repeating rows of the brand mascot silhouette separated by thin black lines"></div>
    <span class="back-brand">KOOLBO</span>
  </section>
</body>
</html>
```